The quiet harbor with an elephant incorporated in the background

Target Market(s)

Real estate

Industry/Entity Type

Real Estate

Contact Information for Business Card

On back on want my name & number
In front I want the business name, "the quiet harbor", below to say staging & design

Logo Text

The quiet harbor

Font styles to use
Serif

Colors
000000

Requirements
Must have
• I want an elephant behind the writing in gold transperant

```html
<!DOCTYPE html>
<html lang="en">
<head>
<meta charset="utf-8">
<title>The Quiet Harbor – Business Card</title>
<link rel="stylesheet" href="https://fonts.googleapis.com/css2?family=Cinzel:wght@400;600&family=Cormorant+Garamond:wght@400;500&display=swap">
<style>
  :root {
    --backdrop: #1c1c1c;
    --card-light: #f4f4f4;
    --card-dark: #3b3b3b;
    --ink-dark: #3a3a3a;
    --ink-soft: #6a6a6a;
    --ink-light: #e8e8e8;
    --rule-light: #d9d9d9;
    --gold-light: #f1d77a;
    --gold-mid: #c9a233;
    --gold-deep: #8a6a14;
  }
  * { box-sizing: border-box; margin: 0; padding: 0; }
  html, body {
    width: 1200px;
    height: 997px;
    overflow: hidden;
    background: var(--backdrop);
  }
  .canvas {
    width: 1200px;
    height: 997px;
    display: flex;
    flex-direction: column;
    align-items: center;
    justify-content: center;
    gap: 56px;
  }
  .card {
    position: relative;
    width: 740px;
    height: 420px;
    border-radius: 22px;
    overflow: hidden;
    box-shadow: 0 14px 34px rgba(0,0,0,0.55);
  }

  /* Back: name and number */
  .card--back {
    background: var(--card-dark);
    color: var(--ink-light);
  }
  .card--back .person-name {
    position: absolute;
    top: 96px;
    width: 100%;
    text-align: center;
    font-family: "Cinzel", serif;
    font-weight: 600;
    font-size: 30px;
    letter-spacing: 1px;
  }
  .card--back .person-role {
    position: absolute;
    top: 146px;
    width: 100%;
    text-align: center;
    font-family: "Cormorant Garamond", serif;
    font-size: 22px;
    letter-spacing: 6px;
  }
  .card--back .emblem-small {
    position: absolute;
    left: 70px;
    top: 214px;
    width: 96px;
    height: 76px;
    border-radius: 6px;
    background: linear-gradient(135deg, var(--gold-mid), var(--gold-deep));
    opacity: 0.75;
  }
  .card--back .divider {
    position: absolute;
    left: 40px;
    right: 40px;
    top: 306px;
    height: 2px;
    background: var(--rule-light);
  }
  .card--back .contact {
    position: absolute;
    top: 328px;
    width: 100%;
    display: flex;
    justify-content: center;
    align-items: center;
    gap: 14px;
    font-family: "Cormorant Garamond", serif;
    font-size: 22px;
    letter-spacing: 1px;
  }
  .contact-icon { width: 32px; height: 32px; }

  /* Front: business name */
  .card--front {
    background: var(--card-light);
    color: var(--ink-dark);
  }
  .card--front .business-name {
    position: absolute;
    top: 64px;
    width: 100%;
    text-align: center;
    font-family: "Cinzel", serif;
    font-weight: 600;
    font-size: 34px;
    letter-spacing: 1px;
  }
  .card--front .business-tagline {
    position: absolute;
    top: 112px;
    width: 100%;
    text-align: center;
    font-family: "Cormorant Garamond", serif;
    font-weight: 500;
    font-size: 20px;
    letter-spacing: 14px;
    color: var(--ink-soft);
  }
  .card--front .emblem-large {
    position: absolute;
    left: 250px;
    top: 160px;
    width: 290px;
    height: 210px;
    border-radius: 10px;
    background: radial-gradient(ellipse at 45% 40%, var(--gold-light), var(--gold-mid) 55%, var(--gold-deep));
  }
</style>
</head>
<body>
<main class="canvas">
  <section class="card card--back">
    <h2 class="person-name">CLAIRE HOLLOWAY</h2>
    <p class="person-role">Design &amp; Staging Consultant</p>
    <div class="emblem-small" role="img" aria-label="Small gold elephant illustration"></div>
    <div class="divider"></div>
    <p class="contact">
      <svg class="contact-icon" viewBox="0 0 32 32" aria-hidden="true">
        <circle cx="16" cy="16" r="16" fill="#e8e8e8"/>
        <rect x="11" y="7" width="10" height="18" rx="2" fill="none" stroke="#3b3b3b" stroke-width="1.8"/>
        <circle cx="16" cy="22" r="1" fill="#3b3b3b"/>
      </svg>
      <span>212-555-0148</span>
    </p>
  </section>

  <section class="card card--front">
    <h1 class="business-name">THE QUIET HARBOR</h1>
    <p class="business-tagline">STAGING &amp; DESIGN</p>
    <div class="emblem-large" role="img" aria-label="Gold elephant illustration with raised trunk"></div>
  </section>
</main>
</body>
</html>
```